New letter head for Air Conditioning business

We need a new professional letter head design to suit our new re-branded air conditioning business. Our new logo is attached

```html
<!DOCTYPE html>
<html lang="en">
<head>
<meta charset="utf-8">
<title>Boreal Air Conditioning &amp; Refrigeration – Letterhead</title>
<link rel="stylesheet" href="https://fonts.googleapis.com/css2?family=Source+Sans+3:wght@400;600;700&display=swap">
<style>
  :root {
    --backdrop: #e9e9e9;
    --paper: #ffffff;
    --ink: #3a3a3a;
    --ink-soft: #6b6b6b;
    --brand-green: #3aa655;
    --brand-red: #e8503e;
    --brand-dark: #2a2a2a;
    --signature-tone: #d6d6d6;
  }
  * { margin: 0; padding: 0; box-sizing: border-box; }
  html, body {
    width: 1200px; height: 795px; overflow: hidden;
    background: var(--backdrop);
    font-family: "Source Sans 3", "Myriad Pro", Arial, sans-serif;
    color: var(--ink);
  }
  .letterhead {
    position: absolute; left: 338px; top: 27px;
    width: 523px; height: 740px;
    background: var(--paper);
    box-shadow: 0 2px 10px rgba(0,0,0,0.12);
  }
  .brand {
    position: absolute; top: 46px; right: 62px;
    display: flex; align-items: center; gap: 8px;
  }
  .brand-dot {
    width: 14px; height: 14px; border-radius: 50%;
    background: var(--brand-green);
  }
  .brand-name {
    font-size: 26px; font-weight: 600; letter-spacing: 3px;
    color: var(--brand-dark); line-height: 1;
  }
  .letter {
    position: absolute; left: 62px; top: 150px; width: 400px;
    font-size: 7.6px; line-height: 1.45; color: var(--ink-soft);
  }
  .date { margin-bottom: 12px; font-size: 8px; }
  .recipient { margin-bottom: 12px; font-size: 8px; }
  .salutation { font-weight: 700; color: var(--ink); font-size: 8.5px; margin-bottom: 10px; }
  .letter p.body { margin-bottom: 10px; }
  .signature {
    position: absolute; right: 70px; top: 440px;
    width: 90px; height: 34px; border-radius: 4px;
    background: linear-gradient(90deg, var(--paper), var(--signature-tone), var(--paper));
  }
  .rule-green {
    position: absolute; left: 230px; right: 28px; top: 500px;
    height: 1.5px; background: var(--brand-green);
  }
  .contact {
    position: absolute; right: 34px; top: 512px;
    text-align: right; font-size: 7.4px; line-height: 1.7; color: var(--ink);
  }
  .contact .company { font-weight: 600; }
  .contact .company .accent-red { color: var(--brand-red); }
  .contact .company .accent-green { color: var(--brand-green); }
  .contact .lines { display: flex; justify-content: flex-end; gap: 6px; align-items: center; }
  .contact .item { display: inline-flex; align-items: center; gap: 3px; }
  .contact svg { width: 7px; height: 7px; }
  .contact .web { color: var(--brand-red); }
  .rule-red {
    position: absolute; left: 28px; right: 260px; top: 580px;
    height: 1.5px; background: var(--brand-red);
  }
</style>
</head>
<body>
  <main class="letterhead">
    <header class="brand">
      <span class="brand-dot"></span>
      <span class="brand-name">BOREAL</span>
    </header>

    <section class="letter">
      <div class="date">January 12, 2014</div>
      <div class="recipient">
        Mr. John Doe<br>President<br>AA Corporation<br>111 Street Name, Suite#<br>City, State, 12345
      </div>
      <div class="salutation">Dear Mr. John,</div>
      <p class="body">Lorem Ipsum is simply dummy text of the printing and typesetting industry. Lorem Ipsum has been the industry's standard dummy text ever since the 1500s, when an unknown printer took a galley of type and scrambled it to make a type specimen book. It has survived not only five centuries, but also the leap into electronic typesetting, remaining essentially unchanged.</p>
      <p class="body">The standard chunk of Lorem Ipsum used since the 1500s is reproduced below for those interested. Sections 1.10.32 and 1.10.33 from "de Finibus Bonorum et Malorum" by Cicero are also reproduced in their exact original form, accompanied by English versions from the 1914 translation by H. Rackham.</p>
      <p class="body">Lorem Ipsum is simply dummy text of the printing and typesetting industry. Lorem Ipsum has been the industry's standard dummy text ever since the 1500s, when an unknown printer took a galley of type and scrambled it to make a type specimen book. It has survived not only five centuries, but also the leap into electronic typesetting, remaining essentially unchanged. It was popularised in the</p>
    </section>

    <div class="signature" role="img" aria-label="Handwritten signature of the sender"></div>

    <div class="rule-green"></div>

    <footer class="contact">
      <div class="company"><span class="accent-red">Boreal</span> <span class="accent-green">Air Conditioning &amp; Refrigeration</span></div>
      <div>Suite 48 Harbour Road, State, Zip 4100, Country</div>
      <div class="lines">
        <span class="item">
          <svg viewBox="0 0 10 10"><circle cx="5" cy="5" r="5" fill="var(--brand-red)"/><path d="M3.2 2.6l1 1-.6.7c.4.8 1 1.4 1.8 1.8l.7-.6 1 1-.8.8C4.6 7 3 5.4 2.6 3.4z" fill="#fff"/></svg>
          (00) 05550 100 200
        </span>
        <span class="item">
          <svg viewBox="0 0 10 10"><circle cx="5" cy="5" r="5" fill="var(--brand-red)"/><rect x="2.5" y="3" width="5" height="4" fill="#fff"/></svg>
          (00) 05550 100 201
        </span>
        <span class="item">
          <svg viewBox="0 0 10 10"><circle cx="5" cy="5" r="5" fill="var(--brand-red)"/><path d="M2.5 3.3h5v3.4h-5z M2.5 3.3l2.5 2 2.5-2" fill="none" stroke="#fff" stroke-width=".8"/></svg>
          hello@borealair.com
        </span>
      </div>
      <div class="web">www.borealair.com</div>
    </footer>

    <div class="rule-red"></div>
  </main>
</body>
</html>
```